Australian Trucking Company Requires Professional Looking Stationary

We require a professional looking stationary design that incorporates our newly designed logo.

Our business, called "Brell Haulage Contracting", provides contracting work, transport and logistics to business in Western Australia particularly with links to the mining sector.

We are a small business looking to expand and our new logo and our new stationary will help develop our brand image in our market place.

Target Market(s)

Businesses and Corporation with links to the Mining Sector

Industry/Entity Type

Small Business

Requirements
Must have
• The letterhead must have the following details:
The new logo

Text saying: "Brell Holdings Pty Ltd (ACN 582 316 907) ATF The Brell Discretionary Trust T/AS"
"ABN 71 834 209 553"
Address "P.O Box 817 Wattlegrove WA, 6958"
Phone: 08 9352 7140
Email: brellhaul@mailbox-example.com.au

The text on the letterhead should be editable as the details are likely to change in the near future. Provision should be made for a website address all though one isn't available at the moment.

The styling, layout and font text is entirely up to the designer.

```html
<!DOCTYPE html>
<html lang="en">
<head>
<meta charset="utf-8">
<title>Brell Haulage Contracting — Business Cards</title>
<link rel="stylesheet" href="https://fonts.googleapis.com/css2?family=Arimo:wght@400;700&display=swap">
<style>
  :root {
    --stage: #ece9e4;
    --card: #ffffff;
    --brand-red: #a3141c;
    --text-dark: #555555;
    --text-mid: #666666;
    --decor-light: #f1f1f1;
    --decor-mid: #d6d6d6;
    --shadow: rgba(0,0,0,0.22);
  }
  * { box-sizing: border-box; margin: 0; padding: 0; }
  html, body { width: 1200px; height: 665px; overflow: hidden; }
  body {
    background: var(--stage);
    font-family: "Arimo", Arial, sans-serif;
    position: relative;
  }
  .card {
    position: absolute;
    top: 170px;
    width: 540px;
    height: 310px;
    background: var(--card);
    box-shadow: 0 6px 18px var(--shadow);
  }
  .card--front { left: 40px; }
  .card--back { left: 620px; }

  .brand {
    position: absolute;
    display: flex;
    align-items: center;
    gap: 12px;
  }
  .brand__mark {
    width: 44px; height: 44px;
    background: var(--decor-mid);
  }
  .brand__name {
    color: var(--brand-red);
    font-weight: 700;
    font-size: 21px;
    line-height: 1.05;
    letter-spacing: 1px;
    text-transform: uppercase;
  }
  .card--front .brand { left: 44px; top: 38px; }
  .card--back .brand { left: 40px; top: 86px; }

  .decor {
    position: absolute;
    width: 180px; height: 150px;
    background: radial-gradient(ellipse at 55% 45%, var(--decor-mid), var(--decor-light) 70%, transparent 100%);
  }
  .card--front .decor { right: 30px; top: 40px; }
  .card--back .decor { right: 30px; top: 120px; }

  .contact {
    position: absolute;
    left: 44px; top: 122px;
    color: var(--text-mid);
  }
  .contact__name {
    font-weight: 700;
    font-size: 16px;
    color: var(--text-dark);
    margin-bottom: 6px;
  }
  .contact__title { font-size: 12px; margin: 0 0 10px 6px; }
  .contact__list { list-style: none; margin-left: 6px; }
  .contact__item {
    display: flex; align-items: center; gap: 8px;
    font-size: 12px; margin-bottom: 6px;
  }
  .contact__icon { width: 11px; height: 11px; fill: var(--text-mid); }

  .legal {
    position: absolute;
    left: 50px; top: 238px;
    font-size: 11.5px;
    color: var(--text-mid);
    line-height: 1.9;
  }

  .web {
    position: absolute;
    left: 50px; top: 248px;
    font-size: 14px;
    letter-spacing: 1.5px;
    color: var(--text-dark);
  }
  .web strong { font-weight: 700; }
</style>
</head>
<body>

<section class="card card--front">
  <div class="brand">
    <span class="brand__mark"></span>
    <span class="brand__name">Brell<br>Haulage<br>Contracting</span>
  </div>
  <div class="decor" role="img" aria-label="Faint grey brand decoration"></div>

  <div class="contact">
    <p class="contact__name">Name here</p>
    <p class="contact__title">Title</p>
    <ul class="contact__list">
      <li class="contact__item">
        <svg class="contact__icon" viewBox="0 0 24 24"><path d="M6.6 10.8a15.1 15.1 0 0 0 6.6 6.6l2.2-2.2a1 1 0 0 1 1-.25 11.4 11.4 0 0 0 3.6.57 1 1 0 0 1 1 1V20a1 1 0 0 1-1 1A17 17 0 0 1 3 4a1 1 0 0 1 1-1h3.5a1 1 0 0 1 1 1c0 1.25.2 2.45.57 3.6a1 1 0 0 1-.25 1z"/></svg>
        08 9352 7140
      </li>
      <li class="contact__item">
        <svg class="contact__icon" viewBox="0 0 24 24"><path d="M2 5h20v14H2z M2 5l10 8 10-8" fill="none" stroke="#666" stroke-width="2.5"/></svg>
        brellhaul@mailbox-example.com.au
      </li>
      <li class="contact__item">
        <svg class="contact__icon" viewBox="0 0 24 24"><g fill="none" stroke="#666" stroke-width="2"><circle cx="12" cy="12" r="10"/><ellipse cx="12" cy="12" rx="4" ry="10"/><path d="M2 12h20"/></g></svg>
        www.brellhaulage.com
      </li>
    </ul>
  </div>

  <div class="legal">
    <p>P.O Box 817 Wattlegrove WA, 6958</p>
    <p>Brell Holdings Pty Ltd (ACN 582 316 907) ATF The Brell Discretionary Trust T/AS</p>
  </div>
</section>

<section class="card card--back">
  <div class="brand">
    <span class="brand__mark"></span>
    <span class="brand__name">Brell<br>Haulage<br>Contracting</span>
  </div>
  <div class="decor" role="img" aria-label="Faint grey brand decoration"></div>
  <p class="web">www.<strong>brellhaulage</strong>.com</p>
</section>

</body>
</html>
```